Harbor Seal Works Spray Foam Appications website

We need a custom website for our company, www.harborsealworks.example. We need something we can modify by adding/changing content, photos, updated projects, etc. We are a commercial contractor specializing in Spray Foam applications. We want the website to be very creative and easy to navigate. The main points of the website are to showcase our projects, and describe our scope of services. We provide spray foam applications to the residential and commercial market. We offer Spray Foam roofing applications, as well as Spray Foam interior insulation applications. We also provide Roof Restoration Coating Systems to refurbish old and failing metal roofs. We would be ok with a one page web design if we can get the scope of our services to flow in a single page. The designer can decide if single or multiple pages works best for our business. One of the suppliers we work with is www.verdansupply.example.

Target Market(s)

Residential Home Builders, General Contractors, Commercial Construction Companies, Property Management Groups.

Industry/Entity Type

Insulation

Number of Pages Required

5+ page

Font styles to use
Serif
Sans Serif

Colors

Designer to choose colors to be used in the design.

Requirements
Must have
• We already have a Wix page, so website must be a Wix theme design. Nice easy to navigate format. Color matched to our current logo theme. We already have brochures and would like for it to match what's already in the hands of some of our customers. Need to be able to manage content to update photos, projects, scope of service, etc., via Wix. Current hold/splash page is hosted at www.harborsealworks.example. We would also like to have this video posted on the home page: https://www.videohost.example/watch?v=QxT4pLm9ZrA&feature=share
Nice to have
• I have attached some splash videos, being able to incorporate these somehow without being overpowering would be nice.

```html
<!DOCTYPE html>
<html lang="en">
<head>
<meta charset="utf-8">
<title>Harbor Seal Works</title>
<link href="https://fonts.googleapis.com/css2?family=Montserrat:wght@400;500;600;700&family=Poppins:wght@300;400;500&display=swap" rel="stylesheet">
<style>
:root{
  --accent:#e8a21b;
  --ink:#1f1f1f;
  --muted:#555;
  --band:#efefef;
  --soft:#f7f7f7;
  --line:#333;
  --white:#fff;
}
*{margin:0;padding:0;box-sizing:border-box}
html,body{width:1200px;height:4498px;overflow:hidden}
body{position:relative;background:var(--white);font-family:'Poppins',sans-serif;color:var(--ink)}
.abs{position:absolute}
.brand{left:0;width:1200px;top:40px;text-align:center}
.brand-mark{width:44px;height:44px;border:3px solid var(--accent);border-radius:50%;margin:0 auto 10px}
.brand-name{font-family:'Montserrat',sans-serif;font-weight:600;font-size:20px;color:var(--accent);letter-spacing:1px}
.nav{left:112px;width:976px;top:150px;border-top:1px solid #ccc;height:72px;display:flex;justify-content:space-between;align-items:center;padding:0 38px;font-family:'Montserrat',sans-serif;font-weight:600;font-size:15px}
.nav a{color:var(--ink);text-decoration:none}
.nav a.active{color:var(--accent)}
.band-top{left:0;top:465px;width:1200px;height:924px;background:var(--band)}
.hero{left:112px;top:222px;width:976px;height:500px;background:linear-gradient(180deg,#1e2f5a 0%,#5b6c88 35%,#8d8466 55%,#c8b170 100%);color:#fff;text-align:center}
.hero h1{font-family:'Montserrat',sans-serif;font-weight:600;font-size:72px;letter-spacing:3px;margin-top:118px}
.hero p{font-family:'Montserrat',sans-serif;font-size:24px;line-height:34px;width:640px;margin:40px auto 0}
.hero .down{position:absolute;left:478px;top:440px}
.about-media{left:112px;top:784px;width:488px;height:500px;background:linear-gradient(135deg,#3b3f9e,#2a2c86 50%,#8b8f9a)}
.play{position:absolute;left:205px;top:205px}
.about-text{left:600px;top:784px;width:488px;height:500px;background:#fff;padding:42px 42px 0 35px}
.about-text h2{font-family:'Montserrat',sans-serif;font-weight:500;font-size:30px;margin-bottom:42px}
.accent{color:var(--accent)}
.about-text p{font-size:13px;line-height:24px;color:var(--muted);text-align:justify;margin-bottom:14px}
.heading{left:0;width:1200px;text-align:center;font-family:'Montserrat',sans-serif;font-weight:500;font-size:31px}
.heading:after{content:"";display:block;width:62px;height:2px;background:var(--ink);margin:14px auto 0}
.heading.plain{font-weight:600;font-size:32px}
.heading.plain:after{display:none}
.services-photo{left:112px;top:1625px;width:976px;height:634px;background:linear-gradient(180deg,#1d2d4c 0%,#4d5a70 40%,#7d838c 60%,#c3c5c8 100%)}
.services-box{left:187px;top:1738px;width:828px;height:404px;background:var(--soft)}
.grid{left:203px;top:1756px;width:794px;height:368px;border:1.5px solid var(--line)}
.cell{position:absolute;border:0.75px solid var(--line);padding:22px 18px 0 18px}
.cell h3{font-family:'Montserrat',sans-serif;font-weight:500;font-size:23px;line-height:24px;margin-bottom:16px;white-space:nowrap}
.cell h3.wrap{white-space:normal}
.cell p{font-size:13px;line-height:21px;color:var(--muted);text-align:justify}
.cell.energy{padding:0 8px 0 96px}
.cell.energy h3{font-size:22px}
.testimonial{left:0;width:1200px;top:2440px;text-align:center}
.quote{font-family:'Montserrat',sans-serif;font-size:27px;line-height:35px;width:570px;margin:0 auto}
.testimonial .who{font-size:17px;margin-top:42px}
.dots{display:flex;gap:6px;justify-content:center;margin-top:28px}
.dots span{width:11px;height:11px;border:1px solid #444;border-radius:50%}
.dots span.on{background:#444}
.band-projects{left:0;top:2699px;width:1200px;height:564px;background:var(--band)}
.card{top:2883px;width:306px;height:300px;background:#fff}
.card .img{height:209px}
.card .label{text-align:center;font-family:'Montserrat',sans-serif;font-size:24px;line-height:91px}
.contact-bg{left:0;top:3263px;width:1200px;height:1235px;background:var(--soft)}
.field{font-size:15px;color:#444;border-bottom:1.5px solid #333;padding-bottom:10px}
.submit{left:548px;top:3681px;width:104px;height:47px;background:#e2e2e2;font-size:15px;color:#444;text-align:center;line-height:47px}
.info-line{left:112px;top:3890px;width:976px;border-top:1.5px solid #555}
.info-sep{top:3891px;width:1.5px;height:100px;background:#555}
.info-label{top:3927px;font-family:'Montserrat',sans-serif;font-weight:500;font-size:19px}
.info-val{top:3962px;font-size:17px;white-space:nowrap}
.map{left:112px;top:4032px;width:976px;height:374px;background:linear-gradient(135deg,#4a4a4a,#3a3a3a 60%,#2e3b44)}
.footer{left:0;width:1200px;top:4448px;text-align:center;font-size:14px}
</style>
</head>
<body>
<div class="abs brand"><div class="brand-mark"></div><div class="brand-name">HARBOR SEAL WORKS</div></div>
<nav class="abs nav"><a class="active">HOME</a><a>ABOUT US</a><a>OUR SERVICES</a><a>WHO WE ARE</a><a>RESOURCES</a><a>CONTACT US</a></nav>

<div class="abs band-top"></div>
<section class="abs hero" role="img" aria-label="Photo of a spray-foamed industrial roof under a dusk sky">
  <h1>HARBOR SEAL</h1>
  <p>We are a commercial contractor specializing in Spray Foam applications.</p>
  <svg class="down" width="20" height="28" viewBox="0 0 20 28"><path d="M10 2v22M4 18l6 7 6-7" stroke="#fff" stroke-width="2" fill="none"/></svg>
</section>

<div class="abs about-media" role="img" aria-label="Spray foam insulation rig trailer, video thumbnail">
  <svg class="play" width="82" height="82" viewBox="0 0 82 82"><circle cx="41" cy="41" r="38" stroke="#fff" stroke-width="4" fill="none"/><path d="M32 24l24 17-24 17z" fill="#fff"/></svg>
</div>
<div class="abs about-text">
  <h2>ABOUT <span class="accent">HARBOR SEAL</span></h2>
  <p>Harbor Seal Works is a Spray Foam and Coating Applications Company with a combined experience of over 20 plus years. We specialize in a diverse range of Spray Foam applications as well as Roof Restoration Coating Systems. Our experiences are that these products provide superior performance and longevity to help our customers reduce energy costs and increase the overall integrity of their assets.</p>
  <p>Spray Polyurethane Foam (SPF) Spray foam is a durable, and versatile product suitable for industrial, commercial, agricultural, and residential applications. It boasts the industry's strongest performance in energy efficiency and energy savings.</p>
</div>

<h2 class="abs heading" style="top:1484px">OUR <span class="accent">SERVICES</span></h2>
<svg class="abs" style="left:592px;top:1555px" width="16" height="28" viewBox="0 0 16 28"><path d="M8 2v22M3 18l5 7 5-7" stroke="#222" stroke-width="2" fill="none"/></svg>

<div class="abs services-photo" role="img" aria-label="Corrugated metal roof stretching toward a dusk sky"></div>
<div class="abs services-box"></div>
<div class="abs grid">
  <div class="cell" style="left:0;top:0;width:263px;height:178px"><h3 class="wrap">Interior Foam Insulation</h3><p>These systems apply to a diverse range of roof types including metal panel.</p></div>
  <div class="cell" style="left:263px;top:0;width:266px;height:178px"><h3 class="wrap">Foam Roof Application</h3><p>This advanced system can be applied to any shape and substrate.</p></div>
  <div class="cell" style="left:529px;top:0;width:263px;height:178px"><h3>Roof Restoration</h3><p style="margin-top:24px">Spray Polyurethane Foam (SPF) Spray foam is a durable, and versatile.</p></div>
  <div class="cell energy" style="left:0;top:178px;width:353px;height:188px">
    <svg style="position:absolute;left:10px;top:52px" width="80" height="80" viewBox="0 0 80 80"><circle cx="40" cy="40" r="35" stroke="#e8a21b" stroke-width="4" fill="none"/><path d="M44 20L30 44h11l-4 17 14-25H40z" stroke="#e8a21b" stroke-width="4" fill="none" stroke-linejoin="round"/></svg>
    <h3 style="margin-top:46px">Energy Conservation</h3><p>These systems apply to a diverse range of roof types including metal panel.</p></div>
  <div class="cell" style="left:353px;top:178px;width:212px;height:188px"><h3 style="margin-top:24px">Fire Retardant</h3><p>This advanced system can be applied to any shape and substrate.</p></div>
  <div class="cell" style="left:565px;top:178px;width:227px;height:188px"><h3 class="wrap">Weather Durability</h3><p>Spray Polyurethane Foam (SPF) Spray foam is a durable, and versatile.</p></div>
</div>

<h2 class="abs heading" style="top:2340px">OUR <span class="accent">TESTIMONIALS</span></h2>
<div class="abs testimonial">
  <p class="quote">“I'm a testimonial. Click to edit me and add text that says something nice about you and your services.”</p>
  <div class="who">— Rowan Ellery</div>
  <div class="dots"><span></span><span class="on"></span><span></span></div>
</div>

<div class="abs band-projects"></div>
<h2 class="abs heading" style="top:2772px">OUR <span class="accent">PROJECTS</span></h2>
<div class="abs card" style="left:112px"><div class="img" role="img" aria-label="Project 1: white foamed roof" style="background:linear-gradient(180deg,#7d9bc0,#c9cdd2 40%,#8e9096)"></div><div class="label">PROJECT1</div></div>
<div class="abs card" style="left:447px"><div class="img" role="img" aria-label="Project 2: coated roof with rooftop units" style="background:linear-gradient(180deg,#9fb3cc,#6e6e6e 35%,#d8d8d6)"></div><div class="label">PROJECT2</div></div>
<div class="abs card" style="left:783px"><div class="img" role="img" aria-label="Project 3: yellow foamed roof on hangar" style="background:linear-gradient(180deg,#3b5c9a,#b8ad92 40%,#e5cf78)"></div><div class="label">PROJECT3</div></div>

<div class="abs contact-bg"></div>
<h2 class="abs heading" style="top:3320px">CONTACT <span class="accent">US</span></h2>
<div class="abs field" style="left:158px;top:3436px;width:430px">Name</div>
<div class="abs field" style="left:612px;top:3436px;width:430px">Email</div>
<div class="abs field" style="left:158px;top:3495px;width:884px">Subject</div>
<div class="abs field" style="left:158px;top:3555px;width:884px;height:82px">Message</div>
<div class="abs submit">Submit</div>

<h2 class="abs heading plain" style="top:3790px">CONTACT INFO</h2>
<div class="abs info-line"></div>
<div class="abs info-sep" style="left:321px"></div>
<div class="abs info-sep" style="left:596px"></div>
<div class="abs info-label" style="left:110px">PHONE</div>
<div class="abs info-val" style="left:110px">555 - 014 - 7890</div>
<div class="abs info-label" style="left:384px">EMAIL</div>
<div class="abs info-val" style="left:384px">info@hsworks.example</div>
<div class="abs info-label" style="left:652px">ADDRESS</div>
<div class="abs info-val" style="left:652px">500 Tern Harbor Street Bayview, CA 94000</div>

<div class="abs map" role="img" aria-label="Street map of the neighbourhood around the office, with location pin"></div>

<div class="abs footer">Copyrights @ 2020 Harbor Seal Works. All Rights Reserved.</div>
</body>
</html>
```